Classy, Elegant, Simple Business Card Design

Looking to have a classy, simple, and elegant design. Want a top notch designed business card. I really like the look of the new torvane credit card. I also like the design I attached. I am trying to reach 21-29 year old females for booking us for there wedding or event. We offer Disc Jockey Service, Photo Booth Rentals, and Uplighting .

Target Market(s)

21-28 year old females

Contact Information for Business Card

Has to have logo, website, email, and phone number

Font styles to use
Other font styles liked:
• open to font choice, modern, clean
Designer to choose
33a6d7
0791cd
0555a3
ffffff

Requirements
Must have
• Has to have logo, website, email, and phone number
Nice to have
• I really like the design of the new torvane credit card. I also included my logo and some designs I like
Should not have
• clutter or too much info

```html
<!DOCTYPE html>
<html lang="en">
<head>
<meta charset="utf-8">
<title>Lumera Event Group – Business Card</title>
<link href="https://fonts.googleapis.com/css2?family=Roboto:wght@400;500;700&display=swap" rel="stylesheet">
<style>
  :root {
    --backdrop: #3a3a3c;
    --card: #1f1f22;
    --silver: #9a9a9e;
    --white: #ffffff;
    --blue-light: #33a6d7;
    --blue: #0791cd;
    --blue-deep: #0555a3;
  }
  * { box-sizing: border-box; margin: 0; padding: 0; }
  html, body { width: 799px; height: 1200px; overflow: hidden; }
  body {
    background: var(--backdrop);
    font-family: "Roboto", Arial, sans-serif;
    display: flex;
    flex-direction: column;
    justify-content: space-around;
    align-items: center;
  }
  .card {
    position: relative;
    width: 620px;
    height: 354px;
    background: var(--card);
    border-radius: 4px;
    box-shadow: 0 18px 40px rgba(0,0,0,0.45);
  }
  /* Front */
  .card-front { display: flex; align-items: center; justify-content: center; }
  .wordmark { text-align: center; font-weight: 500; color: var(--silver); line-height: 1; }
  .wordmark .name { font-size: 58px; letter-spacing: 4px; }
  .wordmark .tagline { font-size: 20px; letter-spacing: 9px; margin-top: 12px; }
  /* Back */
  .card-back .wordmark {
    position: absolute; right: 48px; top: 70px; color: var(--blue);
  }
  .card-back .wordmark .name { font-size: 40px; letter-spacing: 3px; }
  .card-back .wordmark .tagline { font-size: 14px; letter-spacing: 6px; margin-top: 8px; }
  .person { position: absolute; left: 40px; top: 150px; }
  .person-name { color: var(--blue); font-weight: 700; font-size: 22px; }
  .person-role { color: var(--white); font-size: 14px; margin-top: 4px; }
  .rule { position: absolute; height: 2px; background: var(--blue); }
  .rule-top { left: 40px; right: 40px; top: 212px; }
  .rule-bottom { left: 300px; right: 40px; top: 300px; }
  .contacts {
    position: absolute; left: 40px; right: 40px; top: 240px;
    display: flex; justify-content: space-between; list-style: none;
  }
  .contacts li { display: flex; align-items: center; gap: 7px; color: var(--white); font-size: 14px; }
  .contacts svg { width: 14px; height: 14px; fill: var(--blue); flex: none; }
</style>
</head>
<body>
  <section class="card card-front">
    <div class="wordmark">
      <div class="name">LUMERA</div>
      <div class="tagline">EVENT GROUP</div>
    </div>
  </section>

  <section class="card card-back">
    <div class="wordmark">
      <div class="name">LUMERA</div>
      <div class="tagline">EVENT GROUP</div>
    </div>
    <div class="person">
      <div class="person-name">Dana Reyes</div>
      <div class="person-role">Founder &amp; CEO</div>
    </div>
    <div class="rule rule-top"></div>
    <ul class="contacts">
      <li>
        <svg viewBox="0 0 24 24" aria-hidden="true"><path d="M6.6 10.8a15.1 15.1 0 0 0 6.6 6.6l2.2-2.2a1 1 0 0 1 1-.25 11.4 11.4 0 0 0 3.6.57 1 1 0 0 1 1 1V20a1 1 0 0 1-1 1A17 17 0 0 1 3 4a1 1 0 0 1 1-1h3.5a1 1 0 0 1 1 1c0 1.25.2 2.45.57 3.6a1 1 0 0 1-.25 1z"/></svg>
        555 0142 7788
      </li>
      <li>
        <svg viewBox="0 0 24 24" aria-hidden="true"><path d="M2 5h20v14H2z M2 5l10 8 10-8" fill="none" stroke="#0791cd" stroke-width="2"/></svg>
        dana@lumeraevents.com
      </li>
      <li>
        <svg viewBox="0 0 24 24" aria-hidden="true"><circle cx="12" cy="12" r="10"/></svg>
        www.lumeraevents.com
      </li>
    </ul>
    <div class="rule rule-bottom"></div>
  </section>
</body>
</html>
```